Business Cards for new orthopaedic surgery practice

My husband and I are starting our own orthopaedic surgery practice. We are looking for a business card that is uniform, but one will have my name/title and the other will have his. You can just create one design with my name on it for now. But when I choose your design as the winning design I will ask that you add another copy with his name/title.

We are looking for classy, simple, elite all in one. We like dark blues/a little gold/yellow. Something that goes with our logo. We want our logo incorporated. Here is all the info you need:
Business name: RV Bone & Vitality Center
Location: 38517 North Willowmere Ave
Harbor Pines, FL 34829
Phone: 954-218-4063
Fax: 954-582-7341
Email: info@myrvbonecare.example

Names: Lydia Vance, M.D.
Board Certified Hand and Upper Extremity Surgeon

Ebo Dansu, M.D.
Board Certified Hip & Knee Replacement/General Orthopaedic Surgeon

Can decide what you want to put on the back. Maybe a slogan:
Steady Hands. Lasting Strength

I am just going to upload our logo. The only thing is if we select you as the winning design, the location, and phone numbers may change. We will need your help to update that once fully solidified.

Industry/Entity Type

Medical

Contact Information for Business Card

Colors
0054AA
0677BA
7BADD7
CADEEF
E8F1F8
0094D4
00A9DD
6FCCEA
C7EBF8
E9F6FB

Requirements
Must have
• class, appeal,
Should not have
• We want to air on the side of masculine if we are looking at masculine vs. feminine feel. But we still want it classy, sophisticated, and something we will love

```html
<!DOCTYPE html>
<html lang="en">
<head>
<meta charset="utf-8">
<title>RV Bone &amp; Vitality Center – Business Cards</title>
<link href="https://fonts.googleapis.com/css2?family=Tinos:wght@400;700&display=swap" rel="stylesheet">
<style>
  :root {
    --navy: #14224a;
    --gold: #c29a4e;
    --grey-text: #8a8a8a;
    --rule: #9a9a9a;
    --paper: #fbfbfa;
    --backdrop: #e6e6e4;
  }
  * { margin: 0; padding: 0; box-sizing: border-box; }
  html, body {
    width: 1200px; height: 801px; overflow: hidden;
    background: var(--backdrop);
    font-family: "Tinos", "Times New Roman", serif;
  }
  .sheet {
    width: 1200px; height: 801px;
    display: flex; align-items: center; justify-content: center; gap: 40px;
  }
  .card {
    position: relative;
    width: 540px; height: 309px;
    background: var(--paper);
    border-bottom: 3px solid var(--gold);
    border-right: 3px solid var(--gold);
    overflow: hidden;
  }

  /* brand block */
  .brand {
    position: absolute;
    display: flex; flex-direction: column; align-items: center; gap: 12px;
    text-align: center;
  }
  .brand-dot {
    width: 58px; height: 58px; border-radius: 50%;
    background: var(--navy);
  }
  .brand-name {
    color: var(--navy);
    font-weight: 700;
    font-size: 17px;
    letter-spacing: 2px;
    text-transform: uppercase;
    line-height: 1.35;
  }

  /* front: contact side */
  .card-front .brand { left: 28px; top: 90px; width: 210px; }
  .divider {
    position: absolute; left: 258px; top: 58px;
    width: 1px; height: 196px; background: var(--rule);
  }
  .contact { position: absolute; left: 282px; top: 60px; width: 240px; }
  .doctor-name { color: var(--navy); font-weight: 700; font-size: 22px; }
  .doctor-title { color: var(--grey-text); font-size: 14.5px; line-height: 1.25; margin-top: 4px; }
  .contact-list { list-style: none; margin-top: 14px; }
  .contact-list li {
    display: flex; align-items: center; gap: 8px;
    color: var(--grey-text); font-size: 14.5px; line-height: 1.45;
  }
  .contact-list svg { width: 13px; height: 13px; fill: var(--gold); flex: none; }
  .address { color: var(--grey-text); font-size: 14.5px; line-height: 1.3; margin-top: 14px; }

  /* back: slogan side */
  .card-back .brand { left: 0; right: 0; top: 52px; margin: 0 auto; width: 300px; }
  .slogan-band {
    position: absolute; left: 0; right: 0; bottom: 34px; height: 40px;
    background: linear-gradient(90deg, rgba(194,154,78,0) 0%, var(--gold) 28%, var(--gold) 72%, rgba(194,154,78,0) 100%);
    display: flex; align-items: center; justify-content: center;
  }
  .slogan { color: #fff; font-weight: 700; font-size: 19px; letter-spacing: 0.3px; }
</style>
</head>
<body>
<main class="sheet">

  <section class="card card-front" aria-label="Business card, contact side">
    <div class="brand">
      <span class="brand-dot"></span>
      <span class="brand-name">RV Bone &amp;<br>Vitality Center</span>
    </div>
    <div class="divider"></div>
    <div class="contact">
      <h1 class="doctor-name">Lydia Vance, M.D.</h1>
      <p class="doctor-title">Board Certified Hand and<br>Upper Extremity Surgeon</p>
      <ul class="contact-list">
        <li>
          <svg viewBox="0 0 16 16" aria-hidden="true"><path d="M3.6 1.2l2.3 2.7-1.3 1.8c.8 1.9 2.2 3.3 4.1 4.1l1.8-1.3 2.7 2.3-1.3 2.6C6.5 13.4 2.6 9.5 1 3.9z"/></svg>
          954-218-4063
        </li>
        <li>
          <svg viewBox="0 0 16 16" aria-hidden="true"><path d="M4 1h8v4H4zM2 6h12a1 1 0 0 1 1 1v5h-3v3H4v-3H1V7a1 1 0 0 1 1-1zm3 5v3h6v-3z"/></svg>
          954-582-7341
        </li>
        <li>
          <svg viewBox="0 0 16 16" aria-hidden="true"><path d="M1 3h14v10H1zm1.5 1.2L8 8.6l5.5-4.4z"/></svg>
          info@myrvbonecare.example
        </li>
      </ul>
      <p class="address">38517 North Willowmere Ave<br>Harbor Pines, FL 34829</p>
    </div>
  </section>

  <section class="card card-back" aria-label="Business card, slogan side">
    <div class="brand">
      <span class="brand-dot"></span>
      <span class="brand-name">RV Bone &amp;<br>Vitality Center</span>
    </div>
    <div class="slogan-band">
      <p class="slogan">Steady Hands. Lasting Strength</p>
    </div>
  </section>

</main>
</body>
</html>
```